Hot Pilates studio needs window graphics/ front signage

We need window graphics for the front of our hot pilates studio. We have several large front windows that are visible from the street and would be beneficial to have signage. Glow Loft offers several different heated classes on the mat including: Hot Pilates, Sculpt, Hot Barre. I would like for people that drive by to know what we are. The window dimensions are (4 windows) 41 inches X 61 inches, (4 windows) 34 inches X 61 inches (a total of 8 window panels)

Target Market(s)

fit women and men ages 16-65

Industry/Entity Type

fitness, pilates,

Font styles to use
Sans Serif

Colors

Designer to choose only greyscale colors for use in the design.

Requirements
Must have
• HOT PILATES
Nice to have
• our hashtag is #StayRadiant

```html
<!DOCTYPE html>
<html lang="en">
<head>
<meta charset="utf-8">
<title>Glow Loft – Window Graphics</title>
<link href="https://fonts.googleapis.com/css2?family=Montserrat:wght@500;700;800&display=swap" rel="stylesheet">
<style>
  :root{
    --canvas:#ecebea;
    --frame:#1c1c1c;
    --glass-top:#c9c9c9;
    --glass-bottom:#b3b3b3;
    --mullion:#9c9c9c;
    --headline:#ffffff;
    --ink:#1a1a1a;
  }
  html,body{margin:0;padding:0;width:1200px;height:1200px;overflow:hidden;background:var(--canvas);}
  .storefront{
    width:1200px;height:1200px;box-sizing:border-box;
    display:flex;align-items:center;justify-content:center;gap:36px;
    padding:0 40px;
    font-family:"Montserrat",sans-serif;
  }
  .window{
    position:relative;height:420px;box-sizing:border-box;
    border:8px solid var(--frame);
    background:linear-gradient(180deg,var(--glass-top),var(--glass-bottom));
    overflow:hidden;
  }
  .window--side{width:300px;}
  .window--main{width:760px;}
  .window__panes{position:absolute;inset:0;display:flex;}
  .window__pane{flex:1;border-right:4px solid var(--mullion);}
  .window__pane:last-child{border-right:none;}
  .headline{
    position:absolute;left:0;right:0;margin:0;text-align:center;white-space:nowrap;
    color:var(--headline);font-weight:800;letter-spacing:-0.03em;line-height:1;
  }
  .window--side .headline{top:126px;font-size:26px;}
  .window--main .headline{top:100px;font-size:62px;}
  .studio-name{
    position:absolute;left:0;right:0;text-align:center;margin:0;white-space:nowrap;
    color:var(--ink);font-weight:500;letter-spacing:0.04em;
  }
  .window--side .studio-name{top:214px;font-size:16px;}
  .window--main .studio-name{top:236px;font-size:30px;}
  .hashtag-row{
    position:absolute;left:12px;right:12px;bottom:12px;
    display:flex;justify-content:space-between;margin:0;padding:0;list-style:none;
    color:var(--ink);font-weight:700;white-space:nowrap;
  }
  .window--side .hashtag-row{font-size:7px;letter-spacing:0.02em;}
  .window--main .hashtag-row{font-size:13px;letter-spacing:0.04em;}
</style>
</head>
<body>
<main class="storefront">
  <section class="window window--side">
    <div class="window__panes"><div class="window__pane"></div><div class="window__pane"></div><div class="window__pane"></div><div class="window__pane"></div></div>
    <h2 class="headline">SWEAT WITH US</h2>
    <p class="studio-name">Glow Loft</p>
    <ul class="hashtag-row">
      <li>#STAYRADIANT</li><li>#STAYRADIANT</li><li>#STAYRADIANT</li><li>#STAYRADIANT</li>
    </ul>
  </section>
  <section class="window window--main">
    <div class="window__panes"><div class="window__pane"></div><div class="window__pane"></div><div class="window__pane"></div><div class="window__pane"></div></div>
    <h1 class="headline">HOT PILATES &amp; MORE</h1>
    <p class="studio-name">Glow Loft</p>
    <ul class="hashtag-row">
      <li>#STAYRADIANT</li><li>#STAYRADIANT</li><li>#STAYRADIANT</li><li>#STAYRADIANT</li><li>#STAYRADIANT</li><li>#STAYRADIANT</li>
    </ul>
  </section>
</main>
</body>
</html>
```